design a construction company business card

Design business card around our logo. Card must have all the typical info: name, title, address, phone, email, business name, etc. Somewhere on the card I would like to see our motto "Rooted in honesty... Driven by dedication." Consider adding a splash of bright orange to the card to complement the blues and silvers/grays in the logo. We are open to metallic inks, textures, etc. We would like to see options on both light and dark backgrounds. The font in the logo is Euro Technic Extended Regular.

```html
<!DOCTYPE html>
<html lang="en">
<head>
<meta charset="utf-8">
<title>Halden Contracting, Inc. — Business Card</title>
<link href="https://fonts.googleapis.com/css2?family=Michroma&family=Exo+2:wght@400;500&display=swap" rel="stylesheet">
<style>
  :root {
    --backdrop: #e9e9ea;
    --card: #262627;
    --card-edge: #1c1c1d;
    --brand-blue: #2f7fe0;
    --silver: #b7b9bd;
    --text-grey: #a9abaf;
    --panel-grey: #323234;
    --panel-dark: #1b1b1c;
  }
  * { margin: 0; padding: 0; box-sizing: border-box; }
  html, body { width: 1200px; height: 1000px; overflow: hidden; }
  body {
    background: var(--backdrop);
    font-family: "Exo 2", "Segoe UI", sans-serif;
    position: relative;
  }
  .card {
    position: absolute;
    width: 540px;
    height: 310px;
    background: linear-gradient(160deg, #2c2c2e 0%, var(--card) 55%, var(--card-edge) 100%);
    box-shadow: 0 14px 30px rgba(0,0,0,0.28);
    overflow: hidden;
  }
  .card--front { left: 40px; top: 345px; }
  .card--back { left: 620px; top: 345px; }

  .wordmark {
    font-family: "Michroma", "Arial", sans-serif;
    color: var(--brand-blue);
    text-transform: uppercase;
    display: flex;
    align-items: center;
    gap: 8px;
    line-height: 1;
  }
  .wordmark__square {
    width: 10px; height: 10px;
    background: var(--brand-blue);
    flex: none;
  }
  .wordmark__sub { display: block; }
  .card--front .wordmark { position: absolute; left: 28px; top: 34px; font-size: 17px; }
  .card--front .wordmark__sub { font-size: 9px; margin-top: 6px; letter-spacing: 2px; }

  .contact { position: absolute; left: 28px; top: 104px; }
  .contact__name {
    font-family: "Michroma", "Arial", sans-serif;
    color: var(--brand-blue);
    font-size: 13px;
    letter-spacing: 0.5px;
  }
  .contact__title { color: var(--text-grey); font-size: 10px; margin: 4px 0 12px; }
  .contact__address { color: var(--text-grey); font-size: 10px; line-height: 1.35; margin-bottom: 4px; }
  .contact__line {
    display: flex; align-items: center; gap: 6px;
    color: var(--text-grey); font-size: 10px; line-height: 1.6;
  }
  .contact__line svg { width: 9px; height: 9px; flex: none; }
  .contact__line .accent { color: var(--brand-blue); }

  .backdrop-panel { position: absolute; }
  .card--front .backdrop-panel {
    left: 300px; top: 130px; width: 160px; height: 180px;
    background: linear-gradient(180deg, var(--panel-grey), rgba(50,50,52,0));
  }
  .card--back .backdrop-panel {
    left: 0; top: 0; width: 200px; height: 310px;
    background: linear-gradient(90deg, var(--panel-dark), rgba(27,27,28,0));
  }

  .card--back .brand-block { position: absolute; right: 34px; bottom: 52px; }
  .card--back .wordmark { font-size: 26px; }
  .card--back .wordmark__square { width: 14px; height: 14px; }
  .card--back .wordmark__sub { font-size: 11px; margin-top: 8px; letter-spacing: 3px; }
  .motto {
    font-family: "Michroma", "Arial", sans-serif;
    color: var(--brand-blue);
    font-size: 8px;
    letter-spacing: 0.6px;
    text-transform: uppercase;
    margin-top: 14px;
  }
</style>
</head>
<body>
  <section class="card card--front" aria-label="Business card front">
    <div class="backdrop-panel" role="img" aria-label="Faint grey architectural backdrop"></div>
    <div class="wordmark">
      <span class="wordmark__square"></span>
      <span>Halden<span class="wordmark__sub">Contracting, Inc.</span></span>
    </div>
    <div class="contact">
      <p class="contact__name">Marcus Lane</p>
      <p class="contact__title">Managing Director</p>
      <p class="contact__address">2740 Ridgeway Avenue<br>Northfield, ON K2R</p>
      <p class="contact__line">
        <svg viewBox="0 0 10 10"><circle cx="5" cy="5" r="5" fill="#2f7fe0"/><path d="M3.2 2.6l1 1-.6.7a3.5 3.5 0 0 0 2.1 2.1l.7-.6 1 1-.7.8C5 7.3 2.7 5 2.4 3.3z" fill="#262627"/></svg>
        <span>555.014.2200</span>
      </p>
      <p class="contact__line">
        <svg viewBox="0 0 10 10"><circle cx="5" cy="5" r="5" fill="#2f7fe0"/><rect x="2.5" y="3.3" width="5" height="3.4" fill="none" stroke="#262627" stroke-width=".8"/><path d="M2.5 3.3L5 5.3l2.5-2" fill="none" stroke="#262627" stroke-width=".8"/></svg>
        <span>marcus@haldencontract.com</span>
      </p>
      <p class="contact__line">
        <svg viewBox="0 0 10 10"><circle cx="5" cy="5" r="5" fill="#2f7fe0"/><circle cx="5" cy="5" r="2.6" fill="none" stroke="#262627" stroke-width=".8"/><path d="M2.4 5h5.2M5 2.4v5.2" stroke="#262627" stroke-width=".6"/></svg>
        <span>www.<span class="accent">haldencontract</span>.com</span>
      </p>
    </div>
  </section>

  <section class="card card--back" aria-label="Business card back">
    <div class="backdrop-panel" role="img" aria-label="Dark architectural backdrop"></div>
    <div class="brand-block">
      <div class="wordmark">
        <span class="wordmark__square"></span>
        <span>Halden<span class="wordmark__sub">Contracting, Inc.</span></span>
      </div>
      <p class="motto">Rooted in honesty... Driven by dedication.</p>
    </div>
  </section>
</body>
</html>
```